Vehicle Rental Hire in the Algarve - Portugal

We are opening a Vehicle Rental company in the Algarve - Portugal - this will attract both locals and Tourists visiting. So we want this website to capture the beautiful location we will be set in, along with the familiarity of a vehicle rental company. And to keep a colour scheme in Line with out Logo. We are Quenmira Vehicle Rental.

Industry/Entity Type

Vehicle Rental

Number of Pages Required

1 page

Requirements
Must have
• must be professional, and simple to use navigation bar - must also have a "make a reservation" box - similar to the screenshot attached - Under our logo it must read "Vehicle Rental"
Nice to have
• It needs to be in a colour scheme that fits in with our logo

```html
<!DOCTYPE html>
<html lang="en">
<head>
<meta charset="utf-8">
<title>Quenmira Vehicle Rental</title>
<link href="https://fonts.googleapis.com/css2?family=Poppins:wght@400;500;600;700;800&display=swap" rel="stylesheet">
<style>
:root{
  --red:#c42f27;
  --blue:#1c14d8;
  --orange:#ffab00;
  --ink:#333333;
  --text:#444444;
  --light:#f1f1f1;
  --dark:#333333;
  --white:#ffffff;
}
*{margin:0;padding:0;box-sizing:border-box}
html,body{width:1200px;height:3585px;overflow:hidden}
body{font-family:'Poppins',sans-serif;color:var(--text);background:var(--white);position:relative}
.abs{position:absolute}
/* header */
.header{position:absolute;top:0;left:0;width:1200px;height:106px;background:var(--white)}
.brand{position:absolute;left:88px;top:18px;width:136px;height:128px;border-radius:50%;background:var(--white);border:3px solid var(--blue);z-index:3;display:flex;flex-direction:column;align-items:center;justify-content:center;text-align:center}
.brand-name{font-weight:700;font-size:23px;color:var(--blue);line-height:1.1}
.brand-sub{font-weight:700;font-size:12px;color:var(--blue)}
.call{position:absolute;left:718px;top:34px;display:flex;align-items:center;gap:10px}
.call-icon{width:44px;height:44px;border-radius:50%;background:var(--orange);display:flex;align-items:center;justify-content:center}
.call-label{font-size:14px;font-weight:600;color:var(--blue);line-height:1.1}
.call-num{font-size:21px;font-weight:700;color:var(--ink);line-height:1.2}
.partner-btn{position:absolute;left:975px;top:32px;width:152px;height:46px;border:1.5px solid #555;border-radius:24px;font-size:15px;font-weight:600;color:var(--ink);display:flex;align-items:center;justify-content:center}
.nav{position:absolute;top:106px;left:0;width:1200px;height:55px;background:var(--red);display:flex;justify-content:flex-end;align-items:center;gap:34px;padding-right:74px}
.nav a{color:var(--white);font-size:13px;font-weight:600;text-decoration:none}
/* hero */
.hero{position:absolute;top:161px;left:0;width:1200px;height:607px;
  background:
   radial-gradient(ellipse 520px 260px at 760px 250px,rgba(255,214,150,.55),rgba(255,214,150,0) 70%),
   linear-gradient(180deg,#d59a4e 0%,#c07f36 30%,#8a5a2c 52%,#3f2e21 72%,#1b1611 100%)}
.hero-title{position:absolute;right:74px;top:218px;text-align:right;color:var(--white);font-weight:800;font-size:60px;line-height:1}
.hero-sub{position:absolute;right:74px;top:345px;color:var(--white);font-size:34px;font-weight:400}
.dots{position:absolute;left:1063px;top:537px;display:flex;gap:8px}
.dots span{width:9px;height:9px;border-radius:50%;background:var(--white)}
.dots span.on{background:#8e8cff}
.reserve{position:absolute;left:75px;top:238px;width:422px;height:452px;background:var(--white);border-radius:12px;padding:22px 20px 0}
.reserve h2{font-size:29px;font-weight:700;color:var(--ink);margin-left:3px}
.reserve .bar{width:112px;height:4px;background:var(--blue);margin:12px 0 26px 3px}
.field{height:46px;border:1px solid #ccc;border-radius:24px;font-size:14px;color:#333;display:flex;align-items:center;justify-content:space-between;padding:0 22px;margin-bottom:9px}
.row{display:flex;gap:10px}
.row .field{flex:0 0 182px}
.row .field.short{flex:0 0 184px}
.search{height:46px;background:var(--orange);border-radius:24px;color:var(--white);font-size:21px;font-weight:700;display:flex;align-items:center;justify-content:center;margin-top:6px}
/* welcome */
.ring{position:absolute;border-radius:50%;border:6px solid var(--blue)}
.photo{position:absolute;border-radius:50%}
.h-sec{font-size:44px;font-weight:800;color:var(--ink);line-height:1.05}
.h-sec .b{color:var(--blue)}
.para{font-size:14px;line-height:26.5px;color:var(--text)}
.btn-red{position:absolute;width:178px;height:54px;border-radius:28px;background:var(--red);color:var(--white);font-size:16px;font-weight:700;display:flex;align-items:center;justify-content:center}
/* services */
.services{position:absolute;top:1388px;left:0;width:1200px;height:506px;background:linear-gradient(135deg,#3a34e0,#2319d4 60%,#3b36e8)}
.services h2{position:absolute;top:62px;width:100%;text-align:center;color:var(--white);font-size:42px;font-weight:800}
.card{position:absolute;top:142px;width:329px;height:294px;border-radius:10px;overflow:hidden}
.card .img{position:absolute;inset:0}
.card .shade{position:absolute;left:0;right:0;bottom:0;height:110px;background:linear-gradient(180deg,rgba(196,47,39,0),rgba(196,47,39,.95))}
.card span{position:absolute;bottom:18px;width:100%;text-align:center;color:var(--white);font-size:25px;font-weight:700}
/* why */
.why{position:absolute;top:2506px;left:0;width:1200px;height:412px;background:var(--light)}
.why h2{position:absolute;top:52px;width:100%;text-align:center;font-size:42px;font-weight:800;color:var(--ink)}
.why p{position:absolute;top:128px;left:70px;width:1060px;text-align:center;font-size:14px;line-height:27px}
.feat{position:absolute;top:209px;width:240px;text-align:center}
.feat .ic{width:100px;height:100px;border-radius:50%;background:var(--red);border:4px solid var(--blue);border-top-color:var(--red);border-bottom-color:var(--red);margin:0 auto;display:flex;align-items:center;justify-content:center}
.feat .lab{margin-top:22px;font-size:15px;font-weight:600;color:var(--blue)}
/* newsletter */
.news h2{position:absolute;top:2956px;width:1200px;text-align:center;font-size:42px;font-weight:800;color:var(--ink);line-height:1.2}
.news p{position:absolute;top:3021px;width:1200px;text-align:center;font-size:14px}
.email{position:absolute;left:270px;top:3072px;width:478px;height:54px;border:1px solid #ccc;border-radius:28px;font-size:14px;color:#333;padding-left:22px;display:flex;align-items:center}
.sub-btn{position:absolute;left:756px;top:3072px;width:178px;height:54px;background:var(--blue);border-radius:28px;color:var(--white);font-size:17px;font-weight:700;display:flex;align-items:center;justify-content:center}
/* footer */
.footer{position:absolute;top:3189px;left:0;width:1200px;height:396px;background:var(--dark);color:var(--white)}
.f-brand{position:absolute;left:118px;top:80px;width:160px;height:160px;border-radius:50%;border:2px solid #888;display:flex;flex-direction:column;align-items:center;justify-content:center;color:#9a9a9a;text-align:center}
.f-brand b{font-size:24px;font-weight:600;line-height:1.1}
.f-brand i{font-style:normal;font-size:13px;font-weight:600}
.copy{position:absolute;left:40px;top:283px;width:313px;text-align:center;font-size:12px;line-height:20px}
.fcol{position:absolute;top:58px}
.fcol h3{font-size:21px;font-weight:700;margin-bottom:16px}
.fcol li{list-style:none;font-size:13px;line-height:36px}
.contact li{display:flex;gap:14px;line-height:24px;margin-bottom:10px}
.contact svg{flex:0 0 14px;margin-top:5px}
.social{position:absolute;left:884px;top:253px;display:flex;gap:18px}
.social span{width:22px;height:22px;border-radius:50%;border:2px solid var(--white)}
</style>
</head>
<body>

<header class="header">
  <div class="brand"><div class="brand-name">Quenmira</div><div class="brand-sub">Vehicle Rental</div></div>
  <div class="call">
    <div class="call-icon"><svg width="20" height="20" viewBox="0 0 24 24"><path fill="#fff" d="M6.6 10.8a15 15 0 0 0 6.6 6.6l2.2-2.2a1 1 0 0 1 1-.25 11.4 11.4 0 0 0 3.6.57 1 1 0 0 1 1 1V20a1 1 0 0 1-1 1A17 17 0 0 1 3 4a1 1 0 0 1 1-1h3.5a1 1 0 0 1 1 1c0 1.25.2 2.45.57 3.57a1 1 0 0 1-.25 1z"/></svg></div>
    <div><div class="call-label">Call Us</div><div class="call-num">+351 289 000 417</div></div>
  </div>
  <div class="partner-btn">Partner Login</div>
</header>
<nav class="nav">
  <a href="#">FLEET</a><a href="#">PROMOTIONS</a><a href="#">EXTRAS &amp; SERVICES</a><a href="#">ABOUT US</a><a href="#">PARTNERS</a><a href="#">CONTACTS</a><a href="#">RATES AND RESERVATIONS</a>
</nav>

<section class="hero" role="img" aria-label="Luxury car parked in front of a private jet at sunset">
  <div class="hero-title">Looking to Hire<br>Rental Car</div>
  <div class="hero-sub">Book now and get the best offer</div>
  <div class="dots"><span></span><span class="on"></span><span></span><span></span></div>
</section>

<div class="reserve">
  <h2>Make a Reservation</h2>
  <div class="bar"></div>
  <div class="field">Pick up location <span>&#8597;</span></div>
  <div class="field">Driver's age <span>&#8597;</span></div>
  <div class="field">Vehicle category <span>&#8597;</span></div>
  <div class="row"><div class="field">Pick Up date <span>&#9638;</span></div><div class="field short">Hours <span>&#9719;</span></div></div>
  <div class="row"><div class="field">Drop off date <span>&#9638;</span></div><div class="field short">Hours <span>&#9719;</span></div></div>
  <div class="search">Search Now</div>
</div>

<!-- welcome -->
<div class="ring" style="left:77px;top:838px;width:472px;height:472px;border-bottom-color:transparent"></div>
<div class="photo" role="img" aria-label="Colourful hillside Algarve town with a silver sedan in front" style="left:88px;top:852px;width:450px;height:450px;background:linear-gradient(180deg,#2f7fd8 0%,#6fb0ea 22%,#e9b58f 40%,#d98e6a 52%,#efe3d4 68%,#c9ccd1 82%,#aeb2b8 100%)"></div>
<div class="h-sec abs" style="left:618px;top:890px">Welcome to <span class="b">Quenmira</span><br><span class="b">Vehicle Rental</span></div>
<p class="para abs" style="left:617px;top:1005px;width:500px">Sed ut perspiciatis unde omnis iste natus error sit voluptatem accusantium doloremque laudantium, totam rem aperiam, eaque ipsa quae ab illo inventore veritatis et quasi architecto beatae vitae dicta sunt explicabo. Nemo enim ipsam voluptatem quia voluptas sit aspernatur aut odit aut fugit, sed quia consequuntur magni dolores eos qui ratione voluptatem sequi nesciunt.</p>
<div class="btn-red" style="left:617px;top:1201px">Read More</div>

<section class="services">
  <h2>Our Services</h2>
  <div class="card" style="left:75px"><div class="img" role="img" aria-label="Couple in a car receiving keys" style="background:linear-gradient(180deg,#eef0f2 0%,#c9b9ae 45%,#9c7c6c 75%)"></div><div class="shade"></div><span>Fleets</span></div>
  <div class="card" style="left:436px"><div class="img" role="img" aria-label="Smiling saleswoman in a car showroom" style="background:linear-gradient(180deg,#8f9a98 0%,#d8d6d3 45%,#6e767e 75%)"></div><div class="shade"></div><span>Promotions</span></div>
  <div class="card" style="left:796px"><div class="img" role="img" aria-label="Handshake between customers and a dealer" style="background:linear-gradient(180deg,#d3dae0 0%,#8797a8 45%,#4f5a68 75%)"></div><div class="shade"></div><span>Rental Partners</span></div>
</section>

<!-- rates -->
<div class="h-sec abs" style="left:71px;top:2012px">Rates &amp;<br>Reservations</div>
<p class="para abs" style="left:71px;top:2127px;width:500px">Sed ut perspiciatis unde omnis iste natus error sit voluptatem accusantium doloremque laudantium, totam rem aperiam, eaque ipsa quae ab illo inventore veritatis et quasi architecto beatae vitae dicta sunt explicabo. Nemo enim ipsam voluptatem quia voluptas sit aspernatur aut odit aut fugit, sed quia consequuntur magni dolores eos qui ratione voluptatem sequi nesciunt.</p>
<div class="btn-red" style="left:71px;top:2324px">Read More</div>
<div class="ring" style="left:652px;top:1963px;width:472px;height:472px;border-left-color:transparent;border-right-color:transparent"></div>
<div class="photo" role="img" aria-label="Hand holding a phone showing a car rental booking app" style="left:665px;top:1976px;width:446px;height:446px;background:linear-gradient(160deg,#d9dde2 0%,#8c98a6 40%,#3d4652 75%,#2a313a 100%)"></div>

<section class="why">
  <h2>Why Us?</h2>
  <p>Sed ut perspiciatis unde omnis iste natus error sit voluptatem  accusantium doloremque laudantium, totam rem aperiam, eaque ipsa quae ab illo inventore veritatis et quasi architecto beatae vitae dicta sunt explicabo. Nemo enim ipsam voluptatem quia</p>
  <div class="feat" style="left:75px"><div class="ic"><svg width="44" height="40" viewBox="0 0 44 40" fill="none" stroke="#fff" stroke-width="3"><ellipse cx="18" cy="15" rx="15" ry="11"/><path d="M32 12c6 2 9 6 9 10 0 3-2 6-5 8l2 6-7-4c-6 1-12-1-15-5"/></svg></div><div class="lab">24 Hour Assistance</div></div>
  <div class="feat" style="left:343px"><div class="ic"><svg width="42" height="36" viewBox="0 0 42 36" stroke="#fff" stroke-width="4"><line x1="2" y1="6" x2="40" y2="6"/><line x1="2" y1="18" x2="40" y2="18"/><line x1="2" y1="30" x2="40" y2="30"/><rect x="26" y="1" width="6" height="10" fill="#fff"/><rect x="10" y="13" width="6" height="10" fill="#fff"/><rect x="22" y="25" width="6" height="10" fill="#fff"/></svg></div><div class="lab">Fast and customized service</div></div>
  <div class="feat" style="left:618px"><div class="ic"><span style="color:#fff;font-size:40px;font-weight:700">$</span></div><div class="lab">No hidden fees or taxes</div></div>
  <div class="feat" style="left:885px"><div class="ic"><svg width="38" height="32" viewBox="0 0 38 32" fill="#fff"><rect x="0" y="0" width="7" height="7"/><rect x="11" y="0" width="27" height="7"/><rect x="0" y="12" width="7" height="7"/><rect x="11" y="12" width="27" height="7"/><rect x="0" y="24" width="7" height="7"/><rect x="11" y="24" width="27" height="7"/></svg></div><div class="lab">5 Step Booking</div></div>
</section>

<section class="news">
  <h2>Newsletter Subscribe</h2>
  <p>Sed ut perspiciatis unde omnis iste natus error sit voluptatem  accusantium doloremque laudantium, totam rem aperiam,.</p>
  <div class="email">Email Address</div>
  <div class="sub-btn">Subscribe</div>
</section>

<footer class="footer">
  <div class="f-brand"><b>Quenmira</b><i>Vehicle Rental</i></div>
  <div class="copy">Copyright &nbsp;© 2024 Quenmira Vehicle Rental<br>All Right Reserved</div>
  <div class="fcol" style="left:380px"><h3>Site Map</h3><ul><li>Fleet</li><li>Promotions</li><li>Extras &amp; Services</li><li>About Us</li><li>Partners</li><li>Contacts</li><li>Rates And Reservations</li></ul></div>
  <div class="fcol" style="left:634px"><h3>Quick Links</h3><ul><li>Terms and Conditions</li><li>Privacy Policy</li><li>FAQ &amp; Help</li><li>Legal Notice</li></ul></div>
  <div class="fcol contact" style="left:884px"><h3>Contact Us</h3><ul>
    <li><svg width="14" height="12" viewBox="0 0 14 12"><path fill="#fff" d="M0 2l4-2 5 2 5-2v10l-5 2-5-2-4 2z"/></svg><span>14 Rua das Figueiras,<br>Faro 8000-120, Portugal</span></li>
    <li><svg width="14" height="14" viewBox="0 0 24 24"><path fill="#fff" d="M6.6 10.8a15 15 0 0 0 6.6 6.6l2.2-2.2a1 1 0 0 1 1-.25 11.4 11.4 0 0 0 3.6.57 1 1 0 0 1 1 1V20a1 1 0 0 1-1 1A17 17 0 0 1 3 4a1 1 0 0 1 1-1h3.5a1 1 0 0 1 1 1c0 1.25.2 2.45.57 3.57a1 1 0 0 1-.25 1z"/></svg><span>+351 289 000 417</span></li>
    <li><svg width="14" height="11" viewBox="0 0 14 11"><rect width="14" height="11" fill="#fff"/><path d="M0 0l7 6 7-6" stroke="#333" fill="none"/></svg><span>hello@quenmira-rental.pt</span></li>
  </ul></div>
  <div class="social" aria-label="Social links"><span></span><span></span><span></span><span></span><span></span></div>
</footer>

</body>
</html>
```